Yoga site design

we need to design a homepage and content sections for our yoga portal

Verantasa

Verantasa is a yoga community ecosystem dedicated to the yoga enthusiasts and adopters of an active lifestyle based upon yoga and ayurvedic living. The objective of Verantasa is to expand the involvment and adoption of yoga across the communities and facilitate the profitable growth of the various stakeholders and service providers involved with the ecosystem

Site descriptor

The site will have 4 building blocks/functionalities as specified below;

1.Directory functionality wherein it would list yoga classes/events/ workshop/ retreats and show calendar by dates and place
1. when
2. where
3. what
4. who
5. cost
6. durations

2.Search functionality

a.Find a yoga class/studio close to you (location tagging/google maps)
search/show by studioname/ teacher/ Private sessions/ yoga family
1. when
2. where
3. what
4. who
5. cost

3.Content publishing capabilty

a.Micro sites studio directory/ teachers/ frequent event holders/ therapists - contributors and serviceproviders
1. words of descriprion about yourself and your business
2. an email address
3. a live web link
4. google maps
5. contact phone number
6. a logo upload
7. a picture of themselves, (we need to specify size)
8 Weekly/monthly calendar - where thay are and when

b.Topical content
• columns written by a refference or celebrity
• parts in Montly newsletter and/or downloadable

c.Monthly Newsletter

d.What is New/News/Flash Happenings on the Site

e.Community Board
a virtual meeting place on a login and username basis
• Twitter
• chat
• yoganetwork - offline community build
• find a group close to you!

4.E-commerce capability (Yoga store)
by category;
• yoga props
• yoga clothes
• Ayurvedic related products
• Books/Music/dvd
• skin/body
tickets to events -
Updates

Target Market(s)

yoga enthusiasts across multiple cities in europe and americas

Industry/Entity Type

Building

Requirements
Must have
• the design should not be intrusive and allow for multiple city instances to be created using the same deisgn sensibilities
Should not have
• i do not need any tech coding.

```html
<!DOCTYPE html>
<html lang="en">
<head>
<meta charset="utf-8">
<title>Verantasa – Yoga Community</title>
<link href="https://fonts.googleapis.com/css2?family=Crimson+Text:wght@400;600&family=Libre+Baskerville:wght@700&family=Arimo:ital,wght@0,400;0,700;1,400&display=swap" rel="stylesheet">
<style>
:root{
  --backdrop:#f2eee8;
  --page:#ffffff;
  --rust:#b9431f;
  --rust-dark:#a0331a;
  --tan:#d3b48f;
  --tan-bar:#d6b990;
  --teal:#6ec2cf;
  --teal-dark:#4fa3b0;
  --ink:#2a2a2a;
  --blue-title:#1f6fa3;
  --card:#f1efed;
  --card-border:#e3e1de;
  --umber:#2c2119;
  --ice:#b6e0e7;
  --mist:#d6d3cf;
  --logo:#a98a66;
}
*{box-sizing:border-box;margin:0;padding:0}
html,body{width:1200px;height:900px;overflow:hidden}
body{background:var(--backdrop);font-family:"Arimo",Arial,sans-serif;color:var(--ink);position:relative}
.page{position:absolute;left:151px;top:36px;width:896px;height:864px;background:var(--page);box-shadow:0 0 6px rgba(0,0,0,.08)}
.abs{position:absolute}
.brand{left:50px;top:40px;font-family:"Crimson Text",serif;font-weight:600;font-size:42px;letter-spacing:2px;color:var(--logo);display:flex;align-items:center;gap:12px}
.brand .dot{width:14px;height:14px;border-radius:50%;background:var(--logo)}
.header-flourish{left:460px;top:20px;width:400px;height:120px;background:radial-gradient(ellipse at 40% 60%,#f4ead9 0%,rgba(255,255,255,0) 70%)}
.utility{right:40px;top:48px;font-size:12px;color:var(--rust)}
.utility span{color:#ccc;margin:0 7px}
.search{left:673px;top:77px;width:186px;height:24px;border:1px solid #bfbfbf;border-radius:2px;font-style:italic;font-size:11px;color:#888;padding:5px 10px;box-shadow:inset 0 1px 2px rgba(0,0,0,.1)}
.search svg{position:absolute;right:9px;top:5px}
.nav{left:30px;top:122px;width:840px;height:35px;background:var(--rust);font-family:"Crimson Text",serif;font-size:17px;color:#fff}
.nav a{position:absolute;top:0;height:35px;color:#fff;text-decoration:none;padding-top:6px;text-shadow:0 1px 1px rgba(0,0,0,.3);white-space:nowrap}
.nav a.home{left:0;width:74px;background:var(--rust-dark);padding-left:15px}
.hero{left:29px;top:161px;width:842px;height:269px}
.hero-intro{left:0;top:0;width:324px;height:269px;background:var(--tan);text-align:center;color:#fff;font-family:"Crimson Text",serif}
.hero-intro .name{font-size:34px;margin-top:8px}
.hero-intro h1{font-weight:400;font-size:23px;line-height:22px;margin-top:4px;text-shadow:0 1px 1px rgba(0,0,0,.2)}
.hero-intro p{font-family:"Arimo",sans-serif;font-size:12px;line-height:18px;color:#2d2416;margin:12px 16px 0}
.hero-intro .more{font-size:16px;letter-spacing:1px;margin-top:10px;font-weight:600}
.hero-photo{left:325px;top:0;width:517px;height:269px;background:linear-gradient(120deg,#6d6a50 0%,#8c7b5f 30%,#c9977a 55%,#7a6f55 100%);overflow:hidden}
.arrow{width:54px;height:54px;border-radius:50%;background:rgba(255,255,255,.25);top:102px}
.hero-caption{left:0;bottom:-10px;font-family:"Crimson Text",serif;font-size:49px;color:transparent;-webkit-text-stroke:1px rgba(255,255,255,.75);white-space:nowrap}
.ribbon{left:138px;top:484px;width:952px;height:40px}
.ribbon-text{left:178px;top:493px;color:#fff;display:flex;align-items:baseline;width:840px}
.ribbon-text .label{font-family:"Crimson Text",serif;font-size:20px;margin-right:12px}
.ribbon-text .ticker{font-size:12px;flex:1}
.ribbon-text .all{font-size:12px;border-bottom:1px solid #fff}
.card{top:505px;width:265px;height:140px;border:1px solid var(--card-border);padding:5px}
.card-inner{position:relative;width:100%;height:100%;background:var(--card);padding:8px 12px}
.card h2{position:relative;z-index:1;font-family:"Libre Baskerville",serif;font-size:16px;color:var(--blue-title)}
.card h3{position:relative;z-index:1;font-family:"Libre Baskerville",serif;font-size:11px;color:var(--blue-title)}
.card p{font-size:11px;line-height:16px;margin-top:6px;width:205px;position:relative;z-index:1}
.card .figure{position:absolute;right:8px;bottom:6px;width:72px;height:100px;background:linear-gradient(#d6d4d1,#c4c1bd);border-radius:30px 30px 4px 4px;opacity:.8}
.btn{position:absolute;left:11px;bottom:14px;width:92px;height:22px;border-radius:3px;background:linear-gradient(#c0502a,#97301a);color:#fff;font-size:11px;padding:4px 0 0 13px;z-index:1}
.btn::after{content:"";position:absolute;right:12px;top:8px;border-left:5px solid #fff;border-top:3px solid transparent;border-bottom:3px solid transparent}
.finder{left:0;top:659px;width:896px;height:40px;background:var(--tan-bar)}
.finder h2{position:absolute;left:29px;top:7px;font-family:"Crimson Text",serif;font-weight:400;font-size:20px;color:#fff}
.field{position:absolute;top:9px;height:24px;background:#fff;border:1px solid #bfb5a5;font-style:italic;font-size:11px;color:#999;padding:5px 8px}
.submit{position:absolute;left:809px;top:9px;width:74px;height:24px;background:linear-gradient(#fff,#e4e4e4);border:1px solid #aaa;border-radius:2px;font-size:11px;font-weight:700;text-align:center;padding-top:5px;color:#333}
.studios{left:6px;top:714px;width:289px;height:150px}
.studios h2{height:40px;background:var(--umber);color:#fff;font-family:"Crimson Text",serif;font-weight:400;font-size:20px;padding:6px 0 0 15px}
.studios ul{list-style:none;background:var(--ice);height:110px;padding:19px 0 0 20px}
.studios li{font-size:11px;height:25.5px;display:flex;gap:5px;align-items:flex-start}
.body-block{left:321px;top:717px;width:570px;height:147px}
.body-block h2{height:37px;background:var(--mist);color:#fff;font-family:"Crimson Text",serif;font-weight:400;font-size:20px;padding:4px 0 0 9px}
.body-block .paper{position:relative;height:110px;background:#faf6f2;border-top:4px dashed #f0e0dc}
.body-block p{position:absolute;left:13px;top:12px;width:540px;font-size:11px;line-height:17px;color:#ccc}
.map{position:absolute;left:85px;top:12px;width:352px;height:100px;border:5px solid #c9c9c9;background:linear-gradient(135deg,#ece9e0,#e2e6dc 60%,#ddd6c9);opacity:.9}
</style>
</head>
<body>
<div class="page">
  <div class="abs header-flourish" role="img" aria-label="Soft floral flourish in pale cream"></div>
  <div class="abs brand"><span class="dot"></span>Verantasa</div>
  <div class="abs utility">About<span>|</span>Contact<span>|</span>Login</div>
  <div class="abs search">Search...
    <svg width="14" height="14" viewBox="0 0 14 14"><circle cx="5.5" cy="5.5" r="4.3" fill="none" stroke="#555" stroke-width="1.6"/><line x1="8.6" y1="8.6" x2="13" y2="13" stroke="#555" stroke-width="2"/></svg>
  </div>
  <nav class="abs nav">
    <a class="home">Home</a>
    <a style="left:80px">Studios &amp; Teachers</a>
    <a style="left:235px">Events Classes</a>
    <a style="left:352px">Teacher Training</a>
    <a style="left:491px">Corporate Yoga</a>
    <a style="left:621px">Forums</a>
    <a style="left:698px">News</a>
    <a style="left:758px">Style</a>
  </nav>

  <section class="abs hero">
    <div class="abs hero-intro">
      <div class="name">verantasa</div>
      <h1>Welcome To My Yoga<br>Streaming Yoga Globally</h1>
      <p>It has survived not only five centuries, but also the leap into electronic typesetting, remaining essentially unchanged. It was popularised in the 1960s with the release of Pressline sheets containing.</p>
      <div class="more">MORE</div>
    </div>
    <div class="abs hero-photo" role="img" aria-label="Photo of a woman stretching her arms overhead outdoors, eyes closed">
      <div class="abs arrow" style="left:23px"><svg width="54" height="54"><polyline points="31,17 22,27 31,37" fill="none" stroke="#fff" stroke-width="4"/></svg></div>
      <div class="abs arrow" style="right:28px"><svg width="54" height="54"><polyline points="23,17 32,27 23,37" fill="none" stroke="#fff" stroke-width="4"/></svg></div>
      <div class="abs hero-caption">Yoga: A Spiritual Practice</div>
    </div>
  </section>

  <div class="abs card" style="left:29px"><div class="card-inner">
    <h2>Yoga Store</h2><h3>Find your yoga stors local</h3>
    <p>Lorem Ipsum is simply dummy text of the printing and typesetting industry.</p>
    <div class="figure" role="img" aria-label="Silhouette of a yoga pose"></div>
    <div class="btn">Learn More</div>
  </div></div>
  <div class="abs card" style="left:320px"><div class="card-inner">
    <h2>Events &amp; Workshops</h2><h3>Lorem Ipsum is simply dummy text</h3>
    <p>Lorem Ipsum is simply dummy text of the printing and typesetting industry.</p>
    <div class="figure" role="img" aria-label="Silhouette of a seated yoga pose" style="height:60px;width:90px"></div>
    <div class="btn">Learn More</div>
  </div></div>
  <div class="abs card" style="left:607px"><div class="card-inner">
    <h2>Community Board</h2><h3>Lorem Ipsum is simply dummy text</h3>
    <p>Lorem Ipsum is simply dummy text of the printing and typesetting industry.</p>
    <div class="figure" role="img" aria-label="Silhouette of a standing balance pose" style="width:50px;height:92px"></div>
    <div class="btn">Learn More</div>
  </div></div>

  <div class="finder abs">
    <h2>Find Classes, Studios, Teachers, Events</h2>
    <div class="field" style="left:409px;width:195px">All Styles</div>
    <div class="field" style="left:613px;width:195px">Location or post code</div>
    <div class="submit">SUBMIT</div>
  </div>

  <section class="abs studios">
    <h2>Studios Address &amp; Location</h2>
    <ul>
      <li><svg width="9" height="13" viewBox="0 0 9 13"><path d="M4.5 0A4.5 4.5 0 0 0 0 4.5C0 8 4.5 13 4.5 13S9 8 9 4.5A4.5 4.5 0 0 0 4.5 0Z" fill="#4aa9bb"/><circle cx="4.5" cy="4.5" r="1.6" fill="#fff"/></svg>2218 Larkmoor Ave,&nbsp; 40915</li>
      <li><svg width="9" height="13" viewBox="0 0 9 13"><path d="M4.5 0A4.5 4.5 0 0 0 0 4.5C0 8 4.5 13 4.5 13S9 8 9 4.5A4.5 4.5 0 0 0 4.5 0Z" fill="#4aa9bb"/><circle cx="4.5" cy="4.5" r="1.6" fill="#fff"/></svg>1480 Fernhill Rd South, Ashbury Glen, OR 97120</li>
      <li><svg width="9" height="13" viewBox="0 0 9 13"><path d="M4.5 0A4.5 4.5 0 0 0 0 4.5C0 8 4.5 13 4.5 13S9 8 9 4.5A4.5 4.5 0 0 0 4.5 0Z" fill="#4aa9bb"/><circle cx="4.5" cy="4.5" r="1.6" fill="#fff"/></svg>7712 Calder Avenue, Millbrook, OR&nbsp; 97345</li>
      <li><svg width="9" height="13" viewBox="0 0 9 13"><path d="M4.5 0A4.5 4.5 0 0 0 0 4.5C0 8 4.5 13 4.5 13S9 8 9 4.5A4.5 4.5 0 0 0 4.5 0Z" fill="#4aa9bb"/><circle cx="4.5" cy="4.5" r="1.6" fill="#fff"/></svg>315 Dunmore Road, Westvale, OR 97602</li>
    </ul>
  </section>

  <section class="abs body-block">
    <h2>Body content etc...</h2>
    <div class="paper">
      <p>It has survived not only five centuries, but also the leap into electronic typesetting, remaining essentially unchanged. It was popularised with the release of Pressline sheets containing.</p>
      <div class="map" role="img" aria-label="Map showing studio locations marked with pins"></div>
    </div>
  </section>
</div>

<svg class="abs ribbon" viewBox="0 0 952 40" preserveAspectRatio="none" aria-hidden="true">
  <polygon points="0,6 20,6 20,46 0,46 10,26" fill="var(--teal-dark)" transform="translate(0,-6)"/>
  <polygon points="952,6 932,6 932,46 952,46 942,26" fill="var(--teal-dark)" transform="translate(0,-6)"/>
  <rect x="13" y="0" width="926" height="36" fill="var(--teal)"/>
  <polygon points="13,36 13,40 26,36" fill="#3f8692"/>
  <polygon points="939,36 939,40 926,36" fill="#3f8692"/>
</svg>
<div class="abs ribbon-text">
  <span class="label">Latest News:</span>
  <span class="ticker">Welcome to Verantasa It has survived not only five centuries, but also the leap into electronic typesetting, remaining...</span>
  <span class="all">view all news</span>&nbsp;›
</div>
</body>
</html>
```